Electric mountain bike tours nz

We are an Electric Mountain bike tour company in New Zealand. We will be offering bike rental and guided tours around the Nelson region in New Zealand. I want our website to represent both Mountain biking and New Zealand with the colours layout and features. We want tabs for the following:
-1 about us
-2 what we offer
-3 bookings/contact
Under the about us tab will be who we are as a a company. I want the ability to add videos to each of these tabs as we move foward with videos of the tracks we will be riding. I want the website to be editable so I can add and remove videos/photos myself. Also "our bikes" will be under this tab.
Under the what we offer tab will be
-1 bike rental and pricing
-2 guided tours and pricing
-3 recommended package deals.
I want to able to put the tracks under the guided tours tab and select beginner/ intermediate/advanced and have the tracks in each of the following to match the rider level. Also to be able to have a small video of the track would be great in this section.
Bookings and contact tab
(Further information for this tab to be updated soon)
Coded - Design and coding required
1 page
- Silver ferns, kiwi, mountains

```html
<!DOCTYPE html>
<html lang="en">
<head>
<meta charset="utf-8">
<title>KEAVOLT – Electric Mountain Bike Tours in New Zealand</title>
<link href="https://fonts.googleapis.com/css2?family=Open+Sans:wght@400;600;700&display=swap" rel="stylesheet">
<style>
:root{
  --red:#e8401c;
  --ink:#222;
  --text:#444;
  --muted:#666;
  --panel:#f4f4f4;
  --band:#ececec;
  --dark:#1d1d1d;
  --white:#fff;
  --nav:#d9d9d9;
}
*{margin:0;padding:0;box-sizing:border-box}
html,body{width:1200px;height:3614px;overflow:hidden;background:var(--white)}
body{font-family:"Open Sans",Arial,sans-serif;color:var(--text);position:relative}
.abs{position:absolute}
.fill{position:absolute}

/* hero */
.hero{left:0;top:0;width:1200px;height:548px;background:linear-gradient(180deg,#1f2e4a 0%,#34506a 30%,#4c6338 60%,#3b3a20 100%)}
.nav-bar{left:113px;top:34px;width:972px;height:58px;border-radius:29px;background:var(--nav)}
.nav-link{top:34px;height:58px;line-height:58px;font-size:13px;font-weight:700;color:var(--white);letter-spacing:.3px;transform:translateX(-50%)}
.nav-bar .nav-link{color:var(--white)}
.logo-badge{left:522px;top:-10px;width:156px;height:156px;border-radius:50%;background:var(--dark);display:flex;align-items:center;justify-content:center;font-weight:700;font-size:24px;color:var(--white);letter-spacing:1px}
.phone-btn{left:1036px;top:46px;width:36px;height:36px;border-radius:50%;background:var(--dark);display:flex;align-items:center;justify-content:center}
.hero-title{left:0;width:1200px;top:226px;text-align:center;color:var(--white);font-weight:700;font-size:46px;letter-spacing:1px}
.hero-sub{left:0;width:1200px;top:294px;text-align:center;color:var(--white);font-weight:700;font-size:28px}
.btn{display:inline-block;background:var(--red);color:var(--white);font-size:13px;font-weight:700;text-align:center;line-height:32px;height:32px}
.btn-outline{background:transparent;border:2px solid var(--white);line-height:28px}

/* section headings */
.chain{display:flex;gap:3px}
.chain span{width:16px;height:16px;border:4px solid var(--red);border-radius:50%}
.h2{font-weight:700;color:var(--ink);font-size:36px}

/* about */
.bike-img{border-radius:6px}
.callout{width:260px}
.callout b{display:block;color:var(--red);font-size:17px;font-weight:700;margin-bottom:6px}
.callout p{font-size:12.5px;line-height:21px;color:var(--muted)}
.leader{background:var(--muted);height:1px}

/* video */
.panel{background:var(--panel)}
.body-copy{font-size:15px;line-height:21px;color:var(--text)}
.service-title{font-size:21px;font-weight:700;color:var(--ink)}

/* testimonials */
.quote-card{left:629px;top:2395px;width:419px;height:287px;background:var(--red);color:var(--white)}
.quote-card p{font-size:14px;line-height:22px}

/* contact */
.field{left:328px;width:544px;height:48px}
.field .icon{position:absolute;left:0;top:0;width:50px;height:48px;background:var(--red);display:flex;align-items:center;justify-content:center}
.field .box{position:absolute;left:60px;right:0;top:0;bottom:0;border-bottom:1px solid #ddd;font-size:13px;color:var(--muted);padding:14px 0 0 6px}

/* footer */
.footer{left:0;top:3446px;width:1200px;height:111px;background:var(--dark)}
.foot-link{top:3470px;font-size:12px;color:var(--white)}
.social{top:3503px;width:16px;height:16px;border-radius:50%;background:#9ab}
.copyright{left:0;top:3575px;width:1200px;text-align:center;font-size:12px;color:var(--text)}
</style>
</head>
<body>

<!-- HERO -->
<div class="abs hero" role="img" aria-label="Photo of an electric mountain bike on a hilltop above a New Zealand valley at dusk"></div>
<div class="abs nav-bar"></div>
<div class="abs nav-link" style="left:174px">HOME</div>
<div class="abs nav-link" style="left:277px">ABOUT US</div>
<div class="abs nav-link" style="left:414px">WHAT WE OFFER</div>
<div class="abs nav-link" style="left:771px">BOOKINGS</div>
<div class="abs nav-link" style="left:897px">CONTACT US</div>
<div class="abs logo-badge">KEAVOLT</div>
<div class="abs phone-btn">
  <svg width="16" height="16" viewBox="0 0 24 24"><path fill="#fff" d="M6.6 10.8a15 15 0 0 0 6.6 6.6l2.2-2.2a1 1 0 0 1 1-.25 11.4 11.4 0 0 0 3.6.57 1 1 0 0 1 1 1V20a1 1 0 0 1-1 1A17 17 0 0 1 3 4a1 1 0 0 1 1-1h3.5a1 1 0 0 1 1 1c0 1.25.2 2.45.57 3.57a1 1 0 0 1-.25 1z"/></svg>
</div>
<div class="abs hero-title">ELECTRIC MOUNTAIN BIKE</div>
<div class="abs hero-sub">TOURS IN NEW ZEALAND</div>
<a class="abs btn" style="left:446px;top:370px;width:120px">BOOK NOW</a>
<a class="abs btn btn-outline" style="left:581px;top:370px;width:171px">WATCH THE VIDEO</a>

<!-- ABOUT -->
<div class="abs chain" style="left:548px;top:580px"><span></span><span></span><span></span><span></span></div>
<div class="abs h2" style="left:0;width:1200px;text-align:center;top:604px">About The Electric Mountain Bike</div>
<div class="abs bike-img" style="left:272px;top:711px;width:651px;height:361px;background:radial-gradient(ellipse at center,#b9b9b9 0%,#6a6a6a 45%,#fff 72%)" role="img" aria-label="Side view of a silver and black electric mountain bike"></div>

<div class="abs callout" style="left:229px;top:748px"><b>Metus at aliquet</b><p>Quam vehicula vel. Mauris malesuada ac<br>litora amet tortor.</p></div>
<div class="abs leader" style="left:372px;top:760px;width:90px"></div>
<div class="abs callout" style="left:865px;top:706px"><b>Metus at aliquet</b><p>Quam vehicula vel. Mauris malesuada ac<br>litora amet tortor.</p></div>
<div class="abs leader" style="left:700px;top:718px;width:160px"></div>
<div class="abs callout" style="left:894px;top:798px"><b>Metus at aliquet</b><p>Quam vehicula vel. Mauris malesuada ac<br>litora amet tortor.</p></div>
<div class="abs leader" style="left:790px;top:810px;width:100px"></div>
<div class="abs callout" style="left:113px;top:995px"><b>Metus at aliquet</b><p>Quam vehicula vel. Mauris malesuada ac<br>litora amet tortor.</p></div>
<div class="abs leader" style="left:262px;top:1007px;width:60px"></div>
<div class="abs callout" style="left:540px;top:1032px"><b>Metus at aliquet</b><p>Quam vehicula vel. Mauris malesuada ac<br>litora amet tortor.</p></div>

<!-- VIDEO -->
<div class="abs panel" style="left:0;top:1168px;width:1200px;height:505px"></div>
<svg class="abs" style="left:0;top:1168px" width="620" height="505" role="img" aria-label="Photo of an orange mountain bike beside a forest trail sign">
  <defs><linearGradient id="forest" x1="0" y1="0" x2="0" y2="1"><stop offset="0" stop-color="#3e4a2c"/><stop offset=".55" stop-color="#7a5a35"/><stop offset="1" stop-color="#b8793f"/></linearGradient></defs>
  <polygon points="0,0 620,0 513,505 0,505" fill="url(#forest)"/>
  <circle cx="266" cy="240" r="46" fill="#222" fill-opacity=".75"/>
  <polygon points="254,216 254,264 290,240" fill="#fff"/>
</svg>
<div class="abs chain" style="left:670px;top:1216px"><span></span><span></span><span></span><span></span></div>
<div class="abs h2" style="left:670px;top:1236px;font-size:34px">Video</div>
<p class="abs body-copy" style="left:675px;top:1305px;width:434px">Scelerisque justo massa rhoncus aliquam ipsum enim commodo cursus. Elit in lectus. A ac facilisi neque et sed nunc et nisl. Rutrum mus libero. Condimentum phasellus aenean nec iaculis dolor.</p>
<p class="abs body-copy" style="left:675px;top:1410px;width:434px">Scelerisque justo massa rhoncus aliquam ipsum enim commodo cursus. Elit in lectus. A ac facilisi neque et sed nunc et nisl. Rutrum mus libero. Condimentum phasellus aenean nec iaculis dolor.</p>
<a class="abs btn" style="left:670px;top:1546px;width:126px">READ MORE</a>

<!-- SERVICES -->
<svg class="abs" style="left:513px;top:1673px" width="687" height="592" role="img" aria-label="Photo of bush-covered hills overlooking the sea under a blue sky">
  <defs><linearGradient id="coast" x1="0" y1="0" x2="0" y2="1"><stop offset="0" stop-color="#5f86b8"/><stop offset=".35" stop-color="#b7c6d6"/><stop offset=".55" stop-color="#4b5d6a"/><stop offset="1" stop-color="#26321e"/></linearGradient></defs>
  <polygon points="0,0 687,0 687,592 107,592" fill="url(#coast)"/>
</svg>
<div class="abs chain" style="left:110px;top:1710px"><span></span><span></span><span></span><span></span></div>
<div class="abs h2" style="left:110px;top:1728px;font-size:34px;line-height:42px">We provide these<br>services</div>

<svg class="abs" style="left:113px;top:1858px" width="60" height="34" viewBox="0 0 60 34"><g fill="none" stroke="#222" stroke-width="2.5"><circle cx="12" cy="22" r="10"/><circle cx="48" cy="22" r="10"/><path d="M12 22 24 8h16l8 14M24 8l8 14h-20M30 4h6"/></g></svg>
<div class="abs service-title" style="left:183px;top:1858px">Bike rental and pricing</div>
<p class="abs body-copy" style="left:183px;top:1888px;width:340px">Elit in lectus. A ac facilisi neque et sed nunc et nisl. Rutrum mus libero.</p>

<svg class="abs" style="left:113px;top:1951px" width="60" height="34" viewBox="0 0 60 34"><g fill="none" stroke="#222" stroke-width="2.5"><circle cx="12" cy="22" r="10"/><circle cx="48" cy="22" r="10"/><path d="M12 22 24 8h16l8 14M24 8l8 14h-20M30 4h6"/></g></svg>
<div class="abs service-title" style="left:183px;top:1951px">Guided tours and pricing</div>
<p class="abs body-copy" style="left:183px;top:1981px;width:340px">Elit in lectus. A ac facilisi neque et sed nunc et nisl. Rutrum mus libero.</p>

<svg class="abs" style="left:113px;top:2045px" width="60" height="34" viewBox="0 0 60 34"><g fill="none" stroke="#222" stroke-width="2.5"><circle cx="12" cy="22" r="10"/><circle cx="48" cy="22" r="10"/><path d="M12 22 24 8h16l8 14M24 8l8 14h-20M30 4h6"/></g></svg>
<div class="abs service-title" style="left:183px;top:2045px">Recommended package deals</div>
<p class="abs body-copy" style="left:183px;top:2075px;width:340px">Elit in lectus. A ac facilisi neque et sed nunc et nisl. Rutrum mus libero.</p>

<a class="abs btn" style="left:181px;top:2146px;width:127px">READ MORE</a>

<!-- TESTIMONIALS -->
<div class="abs" style="left:0;top:2265px;width:1200px;height:586px;background:var(--band)"></div>
<div class="abs h2" style="left:530px;width:300px;text-align:center;top:2328px">Testimonials</div>
<div class="abs" style="left:116px;top:2410px;width:491px;height:277px;background:radial-gradient(ellipse at center,#555 0%,#2a2a2a 40%,var(--band) 72%)" role="img" aria-label="Side view of a black electric mountain bike"></div>
<div class="abs quote-card">
  <div class="abs" style="left:32px;top:20px;font-size:60px;font-weight:700;line-height:60px">&ldquo;</div>
  <svg class="abs" style="left:330px;top:36px" width="60" height="24" viewBox="0 0 60 24"><path d="M12 2 4 12l8 10M48 2l8 10-8 10" fill="none" stroke="#fff" stroke-opacity=".8" stroke-width="3"/></svg>
  <p class="abs" style="left:32px;top:100px;width:350px">Varius facilisi ipsum. Euismod quis dui suscipit ac vel. Libero turpis a. Malesuada sed elit. Ut blandit orci sociis cursus nullam convallis optio per. Id vel sed nisi nulla odio urna suscipit class. Itaque vel ...</p>
  <div class="abs" style="left:32px;top:206px;font-size:15px;font-weight:600">– Liam Carver</div>
</div>
<div class="abs" style="left:900px;top:2620px;width:150px;height:110px;border-radius:50% 50% 45% 45%;background:#c57b3c" role="img" aria-label="Illustration of a kiwi bird"></div>

<!-- CONTACT -->
<div class="abs h2" style="left:0;width:1200px;text-align:center;top:2891px">Contact Us</div>
<div class="abs field" style="top:3010px"><div class="icon"><svg width="22" height="22" viewBox="0 0 24 24" fill="none" stroke="#fff" stroke-width="2"><circle cx="12" cy="8" r="4"/><path d="M4 21c0-4.5 3.5-7 8-7s8 2.5 8 7z"/></svg></div><div class="box">Name</div></div>
<div class="abs field" style="top:3070px"><div class="icon"><svg width="22" height="22" viewBox="0 0 24 24" fill="none" stroke="#fff" stroke-width="2"><rect x="3" y="5" width="18" height="14"/><path d="m3 5 9 8 9-8"/></svg></div><div class="box">Email</div></div>
<div class="abs field" style="top:3133px"><div class="icon"><svg width="20" height="20" viewBox="0 0 24 24"><path fill="#fff" d="M6.6 10.8a15 15 0 0 0 6.6 6.6l2.2-2.2a1 1 0 0 1 1-.25 11.4 11.4 0 0 0 3.6.57 1 1 0 0 1 1 1V20a1 1 0 0 1-1 1A17 17 0 0 1 3 4a1 1 0 0 1 1-1h3.5a1 1 0 0 1 1 1c0 1.25.2 2.45.57 3.57a1 1 0 0 1-.25 1z"/></svg></div><div class="box">Phone</div></div>
<div class="abs field" style="top:3198px;height:142px"><div class="icon"><svg width="22" height="22" viewBox="0 0 24 24" fill="none" stroke="#fff" stroke-width="2"><path d="M3 4h13v9H8l-5 4z"/><path d="M18 8h3v10l-4-3h-7v-2"/></svg></div><div class="box" style="border:1px solid #ddd">Message</div></div>
<a class="abs btn" style="left:740px;top:3364px;width:132px;height:34px;line-height:34px">SUBMIT</a>

<div class="abs" style="left:0;top:3230px;width:240px;height:200px;background:linear-gradient(120deg,#e2e2e2,#f7f7f7)" role="img" aria-label="Illustration of a silver fern frond with a kiwi bird"></div>
<div class="abs" style="left:960px;top:3210px;width:240px;height:200px;background:linear-gradient(240deg,#e2e2e2,#f7f7f7)" role="img" aria-label="Illustration of a silver fern frond"></div>

<!-- FOOTER -->
<div class="abs footer"></div>
<div class="abs foot-link" style="left:113px">Home</div>
<div class="abs foot-link" style="left:175px">About us</div>
<div class="abs foot-link" style="left:251px">What we offer</div>
<div class="abs foot-link" style="left:357px">Bookings</div>
<div class="abs foot-link" style="left:436px">Contact us</div>
<div class="abs social" style="left:115px"></div>
<div class="abs social" style="left:155px"></div>
<div class="abs social" style="left:195px"></div>
<div class="abs social" style="left:235px"></div>
<div class="abs social" style="left:275px"></div>
<div class="abs" style="left:574px;top:3430px;width:53px;height:110px;background:var(--red);color:var(--white);font-size:12px;font-weight:700;text-align:center">
  <svg width="20" height="14" viewBox="0 0 20 14" style="margin-top:10px"><path d="M3 11 10 4l7 7" fill="none" stroke="#fff" stroke-width="2.5"/></svg>
  <div>TOP</div>
</div>
<div class="abs logo-badge" style="left:913px;top:3435px;width:130px;height:130px;font-size:20px;border:3px solid var(--white)">KEAVOLT</div>
<div class="abs copyright">copyright © 2018 &nbsp; www.keavoltrides.nz</div>

</body>
</html>
```